Meridian Tidewren Pale Ale Beer Label/Badge

We need a Beer Label designed for our first official beer to be launched under The meridian Brand!!
It will be a Pale Ale Called "Tidewren Pale Ale"!

The Meridian has the largest Craft Beer & Cider selection in the Geelong & Surf Coast region. With a funky location and a relaxed vibe, Meridian prides itself on serving delicious, unique seasonal food paired with Australia's best Craft Beer. The meridian is the perfect setting for a relaxed afternoon or evening with friends and can package an experience for larger groups or corporate bookings.

The Meridian Tavern brand has been growing for over a year and a half and the first label needs to integrate The meridian Logo but at the same time bring a fresh, new and eye catching feel to it along with embracing the "Odysseus" story in which we will be naming future beers.

The story of Tidewren is found via the following link
http://lorevault.example/wiki/Tidewren_(folklore)

We expect designers to research The meridian Tavern brand along with the all important Craft Beer Market and demographics. This will, potentially, be the start of many more labels to come for the winning designer!!

Requirements
Must have
• The original "O" needs to be integrated into the new logo and as much as the Greek mythology is being used it needs to be certain that this is an original Australian Craft Beer in the modern age!!
strong, modern & unique!!
Nice to have
• Logo could have a depiction of Tidewren
Should not have
• tackiness or cheap!!

```html
<!DOCTYPE html>
<html lang="en">
<head>
<meta charset="utf-8">
<title>Meridian Tidewren Pale Ale – Label Colourways</title>
<link rel="stylesheet" href="https://fonts.googleapis.com/css2?family=Josefin+Sans:wght@400;600&family=Russo+One&display=swap">
<style>
  :root {
    --canvas: #ffffff;
    --panel: #f4efe2;
    --ink: #2b2724;
    --name-grey: #6d6a66;
    --brand-red: #b3262d;
    --sea: #5f86b8;
    --foam: #d3e2ee;
  }
  html, body {
    margin: 0;
    padding: 0;
    width: 1200px;
    height: 800px;
    overflow: hidden;
    background: var(--canvas);
  }
  .label-range {
    width: 1200px;
    height: 800px;
    display: flex;
    align-items: center;
    justify-content: center;
    gap: 22px;
  }
  .label {
    position: relative;
    width: 212px;
    height: 330px;
    background: var(--label-bg);
    box-shadow: inset 0 0 0 3px var(--accent);
    font-family: "Josefin Sans", Arial, sans-serif;
    color: var(--ink);
  }
  .label--silver { --label-bg: #d9dce0; --accent: #e08a6d; --art-light: #e4e2de; --art: #a9adb3; }
  .label--lime   { --label-bg: #d6e35a; --accent: #7fc8d8; --art-light: #e6efa0; --art: #a8c83a; }
  .label--cream  { --label-bg: #eeeacb; --accent: #6f5a3a; --art-light: #f1ecd0; --art: #d2ca98; }
  .label--amber  { --label-bg: #d9844a; --accent: #8a5a2a; --art-light: #e9dcb8; --art: #b7a57a; }
  .label--rose   { --label-bg: #f0dcdc; --accent: #c79ad0; --art-light: #f3e4dc; --art: #d9a9a0; }

  .label__panel {
    position: absolute;
    top: 30px;
    left: 10px;
    right: 10px;
    bottom: 26px;
    background: var(--panel);
    border: 2px solid var(--accent);
    box-sizing: border-box;
  }
  .label__crest {
    position: absolute;
    top: 10px;
    left: 50%;
    width: 84px;
    height: 36px;
    margin-left: -42px;
    background: var(--panel);
    border: 2px solid var(--accent);
    border-bottom: none;
    border-radius: 42px 42px 0 0;
    box-sizing: border-box;
    z-index: 2;
  }
  .label__crest svg { display: block; }
  .crest-text {
    font-family: "Josefin Sans", Arial, sans-serif;
    font-size: 6px;
    font-weight: 600;
    letter-spacing: 0.6px;
    fill: var(--brand-red);
  }
  .label__brand {
    position: absolute;
    top: 18px;
    left: 0;
    right: 0;
    text-align: center;
    font-size: 19px;
    font-weight: 400;
    letter-spacing: 1.5px;
    color: var(--name-grey);
    line-height: 1;
  }
  .label__artwork {
    position: absolute;
    top: 46px;
    left: 10px;
    right: 10px;
    height: 132px;
    background: linear-gradient(180deg, var(--art-light) 0%, var(--art) 68%, var(--sea) 84%, var(--foam) 100%);
  }
  .label__title {
    position: absolute;
    top: 182px;
    left: 0;
    right: 0;
    text-align: center;
    font-family: "Russo One", Arial, sans-serif;
    font-size: 31px;
    letter-spacing: 1px;
    color: var(--ink);
    line-height: 1;
  }
  .label__style {
    position: absolute;
    top: 219px;
    left: 0;
    right: 0;
    display: flex;
    justify-content: center;
    align-items: center;
    gap: 9px;
    font-size: 11px;
    font-weight: 600;
    letter-spacing: 5px;
    line-height: 1;
  }
  .label__style-dot {
    width: 9px;
    height: 9px;
    border-radius: 50%;
    background: var(--brand-red);
  }
  .label__abv {
    position: absolute;
    top: 240px;
    left: 0;
    right: 0;
    text-align: center;
    font-size: 8px;
    font-weight: 600;
    letter-spacing: 0.5px;
  }
  .label__origin {
    position: absolute;
    bottom: 9px;
    left: 0;
    right: 0;
    text-align: center;
    font-size: 7px;
    color: var(--ink);
  }
</style>
</head>
<body>
<main class="label-range">

  <section class="label label--silver">
    <div class="label__crest">
      <svg width="80" height="34" viewBox="0 0 80 34">
        <path id="arc-silver" d="M10,30 A30,27 0 0 1 70,30" fill="none"/>
        <text class="crest-text"><textPath href="#arc-silver" startOffset="50%" text-anchor="middle" dy="7">HANDCRAFTED BEER</textPath></text>
        <circle cx="40" cy="24" r="7" fill="var(--brand-red)"/>
      </svg>
    </div>
    <div class="label__panel">
      <div class="label__brand">MERIDIAN</div>
      <div class="label__artwork" role="img" aria-label="Illustration of Tidewren rising from the sea against a sunburst, a small ship on the waves"></div>
      <div class="label__title">TIDEWREN</div>
      <div class="label__style"><span>PALE</span><span class="label__style-dot"></span><span>ALE</span></div>
      <div class="label__abv">ABV 5%</div>
    </div>
    <div class="label__origin">Harlow Point, Victoria, Australia</div>
  </section>

  <section class="label label--lime">
    <div class="label__crest">
      <svg width="80" height="34" viewBox="0 0 80 34">
        <path id="arc-lime" d="M10,30 A30,27 0 0 1 70,30" fill="none"/>
        <text class="crest-text"><textPath href="#arc-lime" startOffset="50%" text-anchor="middle">HANDCRAFTED BEER</textPath></text>
        <circle cx="40" cy="24" r="7" fill="var(--brand-red)"/>
      </svg>
    </div>
    <div class="label__panel">
      <div class="label__brand">MERIDIAN</div>
      <div class="label__artwork" role="img" aria-label="Illustration of Tidewren rising from the sea against a sunburst, a small ship on the waves"></div>
      <div class="label__title">TIDEWREN</div>
      <div class="label__style"><span>PALE</span><span class="label__style-dot"></span><span>ALE</span></div>
      <div class="label__abv">ABV 5%</div>
    </div>
    <div class="label__origin">Harlow Point, Victoria, Australia</div>
  </section>

  <section class="label label--cream">
    <div class="label__crest">
      <svg width="80" height="34" viewBox="0 0 80 34">
        <path id="arc-cream" d="M10,30 A30,27 0 0 1 70,30" fill="none"/>
        <text class="crest-text"><textPath href="#arc-cream" startOffset="50%" text-anchor="middle">HANDCRAFTED BEER</textPath></text>
        <circle cx="40" cy="24" r="7" fill="var(--brand-red)"/>
      </svg>
    </div>
    <div class="label__panel">
      <div class="label__brand">MERIDIAN</div>
      <div class="label__artwork" role="img" aria-label="Illustration of Tidewren rising from the sea against a sunburst, a small ship on the waves"></div>
      <div class="label__title">TIDEWREN</div>
      <div class="label__style"><span>PALE</span><span class="label__style-dot"></span><span>ALE</span></div>
      <div class="label__abv">ABV 5%</div>
    </div>
    <div class="label__origin">Harlow Point, Victoria, Australia</div>
  </section>

  <section class="label label--amber">
    <div class="label__crest">
      <svg width="80" height="34" viewBox="0 0 80 34">
        <path id="arc-amber" d="M10,30 A30,27 0 0 1 70,30" fill="none"/>
        <text class="crest-text"><textPath href="#arc-amber" startOffset="50%" text-anchor="middle">HANDCRAFTED BEER</textPath></text>
        <circle cx="40" cy="24" r="7" fill="var(--brand-red)"/>
      </svg>
    </div>
    <div class="label__panel">
      <div class="label__brand">MERIDIAN</div>
      <div class="label__artwork" role="img" aria-label="Illustration of Tidewren rising from the sea against a sunburst, a small ship on the waves"></div>
      <div class="label__title">TIDEWREN</div>
      <div class="label__style"><span>PALE</span><span class="label__style-dot"></span><span>ALE</span></div>
      <div class="label__abv">ABV 5%</div>
    </div>
    <div class="label__origin">Harlow Point, Victoria, Australia</div>
  </section>

  <section class="label label--rose">
    <div class="label__crest">
      <svg width="80" height="34" viewBox="0 0 80 34">
        <path id="arc-rose" d="M10,30 A30,27 0 0 1 70,30" fill="none"/>
        <text class="crest-text"><textPath href="#arc-rose" startOffset="50%" text-anchor="middle">HANDCRAFTED BEER</textPath></text>
        <circle cx="40" cy="24" r="7" fill="var(--brand-red)"/>
      </svg>
    </div>
    <div class="label__panel">
      <div class="label__brand">MERIDIAN</div>
      <div class="label__artwork" role="img" aria-label="Illustration of Tidewren rising from the sea against a sunburst, a small ship on the waves"></div>
      <div class="label__title">TIDEWREN</div>
      <div class="label__style"><span>PALE</span><span class="label__style-dot"></span><span>ALE</span></div>
      <div class="label__abv">ABV 5%</div>
    </div>
    <div class="label__origin">Harlow Point, Victoria, Australia</div>
  </section>

</main>
</body>
</html>
```